We need UI/UX design for a public, informational website for The Copper Lantern.
The pages, structure, and content scope are already defined. Designers are required to work only on the UI/UX layout of these existing pages, focusing on clarity, hierarchy, spacing, and usability. Do not add, remove, rename, or reinterpret pages or content.
The website is strictly informational only. It must not include accounts, onboarding, payments, custody, escrow administration, marketplaces, dashboards, or any transactional functionality.
Scope of work
Apply UI/UX design to the predefined website pages
Design layout for text, images, notices, and sections
Ensure consistent components and layout patterns across page types
Optimize layouts for long form, compliance focused content
Content writing, page creation, and branding changes are out of scope.
Structure reference
The complete page list, hierarchy, and content definitions are provided in the technical documentation and must be treated as the primary source of truth.
A Figma link is provided only as a light visual reference for page existence and structure:
https://meadow-knot-48203956.plumsite.example/
Designers must rely on the documentation for in depth and authoritative reference.
Brand guidelines
The Copper Lantern has existing brand guidelines and official logos, including light and dark versions. These assets will be provided and must be followed exactly. Designers must not redesign, alter, or reinterpret the brand identity.
Look and feel direction
The desired visual direction is inspired by:
https://ledgerwaltz.example/
This reference is provided only to indicate:
Institutional and enterprise tone
Clean, modern typography
Strong hierarchy and generous whitespace
Editorial, content first layouts
Do not copy branding, layouts, components, or assets from the reference site.
Hero section direction
The hero section should follow a similar structural approach to the hero used on https://ledgerwaltz.example/
, meaning:
Strong editorial framing
Clear headline hierarchy
Calm, institutional first impression
However, the background video must be Abu Dhabi focused, not generic or global. The video should visually reflect:
Abu Dhabi skyline or architectural language
Institutional, sovereign, long term infrastructure tone
Clean, slow, cinematic motion
No promotional, marketing, or lifestyle visuals
The hero must remain informational, restrained, and credible. No hype. No calls to invest. No implied participation.
Constraints
One global primary CTA only: “Continue to Halvemark” (external)
All other interactions must be informational
No visuals or language implying offers, investment, eligibility, or participation
Clear separation between informational content and any external operational platforms
Deliverables
High fidelity UI/UX designs created in Figma, covering:
Desktop layouts
Tablet layouts where relevant
Mobile layouts
Complete Figma file(s) including:
All designed pages defined in the technical documentation
A reusable component library (headers, footers, cards, notice panels, forms, CTAs, typography styles, spacing system)
Clearly defined layout grids, spacing rules, and text styles
Proper use of components and variants, not detached frames
Designs prepared for developer handoff, including:
Clear layer naming and structure
Auto layout where appropriate
Consistent use of styles and components
Responsive behavior demonstrated within Figma
Notes or annotations only where necessary for clarity
No prototypes, interactions, or motion design beyond basic layout states, unless explicitly requested. The focus is static UI/UX clarity, not animation.
A detailed technical specification document and official brand assets will be provided.
Any designs delivered outside Figma, that alter structure or content, or that ignore the defined constraints, boundaries, or tone will be rejected.

```html
<!DOCTYPE html>
<html lang="en">
<head>
<meta charset="utf-8">
<title>The Copper Lantern — Page Designs</title>
<link href="https://fonts.googleapis.com/css2?family=Manrope:wght@400;500;600;700&display=swap" rel="stylesheet">
<style>
:root{
  --canvas:#b1b1b1;
  --ink:#000;
  --paper:#fff;
  --panel:#f0f3f8;
  --charcoal:#2b2b2b;
  --mute:#555;
  --mute-dark:#bdbdbd;
  --line:#cfd3da;
  --line-dark:#3a3a3a;
}
*{margin:0;padding:0;box-sizing:border-box}
html,body{width:1200px;height:1007px;overflow:hidden;background:var(--canvas)}
body{font-family:"Manrope",sans-serif;color:var(--ink);font-size:4px;line-height:1.3}
.board{position:relative;width:2100px;height:1763px;transform:scale(.571428);transform-origin:0 0}
.page{position:absolute;width:476px;background:var(--paper);overflow:hidden;box-shadow:0 2px 8px rgba(0,0,0,.18)}
.p-home{left:49px;top:49px;height:1577px}
.c2{left:558px}.c3{left:1067px}.c4{left:1576px}
.r1{top:49px;height:816px}.r2{top:898px;height:816px}

/* nav */
.nav{position:absolute;top:0;left:0;right:0;height:26px;display:flex;align-items:center;justify-content:space-between;padding:0 9px;color:var(--paper);z-index:2}
.brand{font-size:4.6px;font-weight:600;letter-spacing:.2px;white-space:nowrap}
.nav-links{display:flex;gap:10px;font-size:4px;color:var(--mute-dark)}
.nav-links .on{color:var(--paper)}
.nav-cta{background:var(--paper);color:var(--ink);font-size:4px;font-weight:700;padding:2.5px 6px;border-radius:6px}

/* hero */
.hero{position:relative;height:172px;display:flex;flex-direction:column;align-items:center;justify-content:center;text-align:center;color:var(--paper);padding:30px 90px 0}
.hero-photo{position:absolute;inset:0;background:linear-gradient(180deg,#1d1d1d 0%,#3a3a3a 45%,#262626 100%)}
.hero-photo::after{content:"";position:absolute;inset:0;background:rgba(0,0,0,.35)}
.hero h1,.hero p,.hero .pill{position:relative}
.hero h1{font-size:16.5px;font-weight:500;letter-spacing:-.2px;line-height:1.2}
.hero p{font-size:7px;line-height:1.4;margin-top:5px;color:#e4e4e4}
.hero-home{height:270px;padding:60px 110px 0}
.hero-home .hero-photo{background:linear-gradient(180deg,#3c3c3c 0%,#555 35%,#3e3e3e 70%,#242424 100%)}
.pill{display:inline-block;font-size:4.2px;font-weight:600;padding:3px 9px;border-radius:8px;margin-top:8px;line-height:1.2}
.pill-light{background:var(--paper);color:var(--ink)}
.pill-outline{border:.7px solid var(--paper);color:var(--paper)}
.pill-dark{background:var(--ink);color:var(--paper)}

.notice{height:26px;display:flex;align-items:center;justify-content:center;font-size:5.3px;letter-spacing:.3px;border-bottom:.6px solid var(--line)}

.eyebrow{font-size:3.6px;color:var(--mute);margin-bottom:2px}
.sec-title{font-size:11.5px;font-weight:600;line-height:1.2;letter-spacing:-.1px}
.small{font-size:3.5px;line-height:1.45;color:#333}

/* intro */
.intro{height:133px;background:var(--panel);display:grid;grid-template-columns:158px 1fr;gap:18px;padding:34px 50px 0 68px}
.intro .small{margin-top:5px}
.intro h3{font-size:5.6px;font-weight:600;margin:11px 0 4px}
.checks{list-style:none}
.checks li{font-size:3.5px;line-height:1.55;display:flex;gap:3px;align-items:center}
.checks li::before{content:"";width:3px;height:1.6px;border-left:.7px solid var(--ink);border-bottom:.7px solid var(--ink);transform:rotate(-45deg) translateY(-.6px)}
.checks.cross li::before{width:2.6px;height:2.6px;border:none;background:linear-gradient(45deg,transparent 42%,var(--ink) 42%,var(--ink) 58%,transparent 58%),linear-gradient(-45deg,transparent 42%,var(--ink) 42%,var(--ink) 58%,transparent 58%);transform:none}

/* scope */
.scope{height:98px;background:var(--ink);color:var(--paper);display:grid;grid-template-columns:158px 1fr;gap:18px;padding:32px 50px 0 68px}
.scope .eyebrow{color:#9a9a9a}
.scope .small{color:#e0e0e0;margin-top:6px}
.scope .pill{margin-top:6px}

/* why */
.why{height:174px;background:var(--panel);text-align:center;padding:28px 68px 0}
.why .small{margin:5px auto 0;max-width:340px;font-size:3.2px}
.why-grid{display:grid;grid-template-columns:1fr 1fr;margin-top:12px}
.why-cell{padding:7px 8px 9px}
.why-cell:nth-child(1),.why-cell:nth-child(2){border-bottom:.6px solid var(--line)}
.why-cell:nth-child(odd){border-right:.6px solid var(--line)}
.why-cell h4{font-size:4.4px;font-weight:600;margin-bottom:3px}
.why-cell p{font-size:3.1px;line-height:1.45;color:#444}

/* cta */
.cta{height:123px;background:var(--charcoal);color:var(--paper);text-align:center;padding:28px 100px 0}
.cta .eyebrow{color:#cfcfcf;letter-spacing:.3px}
.cta h2{font-size:11.5px;font-weight:600;line-height:1.2}
.cta p{font-size:4.2px;color:#cfcfcf;margin-top:4px;line-height:1.4}
.cta .pill{margin-top:6px}

/* footer */
.foot{height:116px;background:var(--ink);color:var(--paper);padding:16px 68px 0}
.foot-top{display:grid;grid-template-columns:82px repeat(6,1fr);gap:6px}
.foot-brand p{font-size:3px;line-height:1.4;color:#bbb;margin-top:4px}
.foot-col b{display:block;font-size:4.2px;font-weight:500;margin-bottom:2px}
.foot-col span{display:block;font-size:3px;line-height:1.45;color:#bbb}
.foot-col .big{font-size:4.4px;color:var(--paper);margin-top:3px}
.foot-base{display:grid;grid-template-columns:50px 90px 110px 1fr;gap:8px;margin-top:22px;padding-top:8px;border-top:.6px solid var(--line-dark);font-size:3px;color:#bbb;line-height:1.4}
.foot-base b{color:var(--paper);font-weight:600;font-size:3.4px}

/* home sections */
.about{height:406px;background:var(--panel);padding:38px 68px 0}
.about-top{display:grid;grid-template-columns:170px 1fr;gap:8px}
.about-top .small{margin-top:5px}
.about-top .pill{margin-top:5px}
.tiles{display:grid;grid-template-columns:repeat(3,1fr);gap:2px;height:98px}
.tile{position:relative;background:linear-gradient(180deg,#2f2f2f,#555 60%,#3a3a3a)}
.tile span{position:absolute;left:5px;bottom:4px;font-size:4px;color:var(--paper);line-height:1.2}
.role-head{text-align:center;margin-top:38px}
.role-cards{display:grid;grid-template-columns:repeat(3,1fr);gap:12px;margin-top:8px}
.role-card{background:var(--paper)}
.role-img{height:65px;background:linear-gradient(180deg,#3a3a3a,#6a6a6a 70%,#444)}
.role-body{padding:6px 8px 7px}
.role-body h4{font-size:6px;font-weight:600;line-height:1.2}
.role-body .small{font-size:3px;margin-top:3px}
.meta{display:grid;grid-template-columns:25px 1fr;font-size:3px;margin-top:3px;row-gap:2px}
.meta dt{color:#666}.meta dd{font-weight:600}

.framework{height:291px;background:var(--ink);color:var(--paper);display:grid;grid-template-columns:146px 1fr;padding:36px 68px 0}
.framework .eyebrow{color:#999}
.framework .small{color:#ddd;margin-top:8px;font-size:3.4px;max-width:100px}
.fw-item{border-bottom:.6px solid var(--line-dark);padding:0 0 9px;margin-bottom:16px}
.fw-item i{display:block;font-style:normal;font-size:3.2px;color:#999;line-height:1.3}
.fw-item h4{font-size:7px;font-weight:500;margin:3px 0 2px;line-height:1.2}
.fw-item p{font-size:3.2px;color:#bbb;line-height:1.4}

.reviewers{height:170px;background:var(--paper);text-align:center;padding:34px 68px 0}
.reviewers .sec-title{font-size:11px}
.reviewers .small{font-size:3.2px;margin-top:3px}
.rev-grid{display:grid;grid-template-columns:repeat(4,1fr);gap:9px;margin-top:9px}
.rev-box{border:1px solid #9a9a9a;height:66px;text-align:left;padding:8px 8px}
.rev-box h4{font-size:5px;font-weight:600;line-height:1.15}
.rev-box p{font-size:3.1px;color:#444;line-height:1.4;margin-top:3px}

/* contact form */
.form-band{height:98px;background:var(--ink);color:var(--paper);display:grid;grid-template-columns:166px 1fr;gap:10px;padding:24px 68px 0}
.form-band .eyebrow{color:#999}
.form-band .small{color:#ccc;margin-top:3px}
.form-grid{display:grid;grid-template-columns:1fr 1fr;column-gap:10px;row-gap:6px}
.field{border-bottom:.6px solid #777;font-size:3.4px;padding-bottom:4px;color:#ddd}
.field.wide{grid-column:1/3;height:16px}
.form-foot{display:flex;align-items:center;gap:12px;margin-top:6px}
.form-foot .pill{margin-top:0}
.form-foot span{font-size:3px;color:#aaa;max-width:70px;line-height:1.3}
.intro h3.tight{margin-top:0}
</style>
</head>
<body>
<div class="board">

<!-- HOME -->
<section class="page p-home">
  <header class="nav"><div class="brand">THE COPPER LANTERN</div><nav class="nav-links"><span class="on">Home</span><span>Frameworks</span><span>Projects</span><span>Halvemark</span><span>Insights</span><span>Company</span><span>Contact</span></nav><span class="nav-cta">Continue to Halvemark</span></header>
  <div class="hero hero-home">
    <div class="hero-photo" role="img" aria-label="Monochrome aerial view of a coastal city skyline and waterfront"></div>
    <h1>Governance Intelligence for<br>Long-Term Systems</h1>
    <p>Research-led frameworks and foresight for<br>complex governance environments</p>
    <span class="pill pill-outline" style="background:rgba(0,0,0,.3)">View Frameworks</span>
  </div>
  <div class="notice">Informational governance research only. No execution, administration, or operational control.</div>
  <div class="about">
    <div class="about-top">
      <div>
        <div class="eyebrow">About The Copper Lantern</div>
        <h2 class="sec-title">From Governance<br>Frameworks to<br>Institutional Insight</h2>
        <p class="small">The Copper Lantern examines governance structures, institutional frameworks, and decision-making models across complex project environments. Our work focuses on research, analysis, and the articulation of principles that inform long-term governance thinking without participating in operational execution.</p>
        <span class="pill pill-dark">Our Framework</span>
      </div>
      <div class="tiles">
        <div class="tile" role="img" aria-label="Monochrome tower facade"><span>Clear Role<br>Separation</span></div>
        <div class="tile" role="img" aria-label="Monochrome office building"><span>Independent<br>Governance<br>Principles</span></div>
        <div class="tile" role="img" aria-label="Monochrome curved tower"><span>Institutional-Grade<br>Standards</span></div>
      </div>
    </div>
    <div class="role-head"><div class="eyebrow">Role Clarity</div><h2 class="sec-title">Our Role Within the Governance Landscape</h2></div>
    <div class="role-cards">
      <div class="role-card"><div class="role-img" role="img" aria-label="Monochrome classical institutional building"></div><div class="role-body"><h4>Governance<br>Framework Analysis</h4><p class="small">We study governance frameworks and institutional structures to understand how authority, accountability, and decision rights are defined across complex environments.</p><dl class="meta"><dt>Category</dt><dd>Governance Research &amp; Frameworks</dd><dt>Audience</dt><dd>Institutional, Academic &amp; Public Reference</dd><dt>Disclosure</dt><dd>Informational Use Only - Not Operational or Advisory</dd></dl></div></div>
      <div class="role-card"><div class="role-img" role="img" aria-label="Monochrome high-rise facade"></div><div class="role-body"><h4>Operational Boundary<br>Definition</h4><p class="small">This work documents where governance stops and execution begins, establishing conceptual boundaries without involvement in management or operations.</p><dl class="meta"><dt>Category</dt><dd>Governance Research &amp; Frameworks</dd><dt>Audience</dt><dd>Institutional, Academic &amp; Public Reference</dd><dt>Disclosure</dt><dd>Informational Use Only - Not Operational or Advisory</dd></dl></div></div>
      <div class="role-card"><div class="role-img" role="img" aria-label="Monochrome city towers"></div><div class="role-body"><h4>Transaction-Agnostic<br>Perspective</h4><p class="small">Our perspective remains neutral and non-transactional, focused on principles and structural insight rather than financial activity or execution.</p><dl class="meta"><dt>Category</dt><dd>Governance Research &amp; Frameworks</dd><dt>Audience</dt><dd>Institutional, Academic &amp; Public Reference</dd><dt>Disclosure</dt><dd>Informational Use Only - Not Operational or Advisory</dd></dl></div></div>
    </div>
  </div>
  <div class="framework">
    <div><div class="eyebrow">Core Governance Principles</div><h2 class="sec-title">The Framework</h2><p class="small">A reference framework outlining governance principles, structural boundaries, and institutional design considerations.</p></div>
    <div>
      <div class="fw-item"><i>01</i><h4>Role Boundaries</h4><p>Defines conceptual boundaries between governance entities, operational platforms, and execution responsibilities for institutional reference.</p></div>
      <div class="fw-item"><i>02</i><h4>SPV Structure</h4><p>Outlines reference structures for special purpose vehicles, focusing on isolation, accountability design, and structural clarity at a framework level.</p></div>
      <div class="fw-item"><i>03</i><h4>Escrow Model</h4><p>Presents non-operational reference models describing conditional custody concepts and third-party structural roles in governed environments.</p></div>
      <div class="fw-item"><i>04</i><h4>Records and Registers</h4><p>Documents record-keeping principles, transparency standards, and informational registries used for governance analysis and reference.</p></div>
      <div class="fw-item"><i>05</i><h4>Risk and Boundaries</h4><p>Explores risk classification principles and boundary definitions used to evaluate responsibility separation in institutional frameworks.</p></div>
    </div>
  </div>
  <div class="reviewers">
    <h2 class="sec-title">For Framework Reviewers</h2>
    <p class="small">This section is intended for institutional, academic, and professional audiences reviewing governance frameworks for reference, comparison, and analytical understanding. Content<br>is provided to support interpretation of governance principles, structural boundaries, and conceptual models without operational participation or advisory intent.</p>
    <div class="rev-grid">
      <div class="rev-box"><h4>Review Governance<br>Structures</h4><p>Explore published frameworks outlining governance models, role separation, and accountability principles.</p></div>
      <div class="rev-box"><h4>Defined Structural<br>Ownership</h4><p>Frameworks clarify responsibility and authority boundaries without operational or transactional execution.</p></div>
      <div class="rev-box"><h4>Operational<br>Independence</h4><p>Execution, asset handling, and platform operations occur outside this site through independent entities.</p></div>
      <div class="rev-box"><h4>Clear Access<br>Boundaries</h4><p>This site provides documentation and reference materials only—no onboarding, custody, or execution.</p></div>
    </div>
  </div>
  <div class="why">
    <h2 class="sec-title">Why The Copper Lantern</h2>
    <p class="small">Our work focuses on the research, analysis, and documentation of governance frameworks across complex institutional environments. Our publications emphasize clarity, structural integrity, and long-term perspective, supporting informed understanding of governance systems without assuming operational roles or authority.</p>
    <div class="why-grid">
      <div class="why-cell"><h4>Governance-First Approach</h4><p>We prioritize structural clarity and accountability, treating governance<br>as the foundation—not an afterthought.</p></div>
      <div class="why-cell"><h4>Proven Structural Principles</h4><p>Our frameworks are informed by institutional standards across governance,<br>compliance, and long-term infrastructure design.</p></div>
      <div class="why-cell"><h4>Bridging Structure &amp; Execution</h4><p>We define governance and role boundaries while execution occurs<br>independently through separate operational platforms.</p></div>
      <div class="why-cell"><h4>Defined Control &amp; Boundaries</h4><p>Clear limitations ensure responsibilities remain properly scoped,<br>auditable, and enforceable.</p></div>
    </div>
  </div>
  <div class="cta"><div class="eyebrow">FOR PROJECT ORIGINATORS</div><h2>Governance Frameworks and<br>Reference Materials</h2><p>Published research, structural frameworks, and reference<br>materials for institutional review.</p><span class="pill pill-dark">Explore Governance Frameworks</span></div>
  <footer class="foot" style="height:117px">
    <div class="foot-top">
      <div class="foot-brand"><div class="brand">THE COPPER LANTERN</div><p>Governance frameworks, institutional research, and reference materials focused on structural design, boundaries, and long-term governance principles.</p></div>
      <div class="foot-col"><b>Frameworks</b><span>Framework Overview</span><span>Role Boundaries</span><span>SPV Structure</span><span>Escrow Model</span><span>Records &amp; Registers</span><span>Risk &amp; Boundaries</span></div>
      <div class="foot-col"><b>Projects</b><span>Projects</span><span class="big">Halvemark</span><span>Halvemark</span></div>
      <div class="foot-col"><b>Insights</b><span>Insights</span><span>Research Publications</span><span>Analysis &amp; Commentary</span></div>
      <div class="foot-col"><b>Company</b><span>About</span><span>Leadership</span><span>Governance</span><span>Press</span><span>Careers</span></div>
      <div class="foot-col"><b>Legal</b><span>Privacy</span><span>Cookie</span><span>Disclaimer &amp; Risk Notice</span><span>Acceptable Use</span><span>Accessibility</span></div>
      <div class="foot-col"><b>Contact</b><span>Contact</span><span>Request Information</span><span>Partners</span><span class="big">Glossary</span><span>Glossary</span></div>
    </div>
    <div class="foot-base"><b>Jurisdiction &amp; Disclosure</b><p>Registered in the Harbour Free Zone Registry (HFZR). Global scope, jurisdiction-neutral research and foresight.</p><p>This website provides informational and reference materials only. No content constitutes operational, legal, financial, or investment advice.</p><p>© The Copper Lantern. All rights reserved.</p></div>
  </footer>
</section>

<!-- GOVERNANCE FRAMEWORKS -->
<section class="page c2 r1">
  <header class="nav"><div class="brand">THE COPPER LANTERN</div><nav class="nav-links"><span class="on">Home</span><span>Frameworks</span><span>Projects</span><span>Halvemark</span><span>Insights</span><span>Company</span><span>Contact</span></nav><span class="nav-cta">Continue to Halvemark</span></header>
  <div class="hero"><div class="hero-photo" role="img" aria-label="Monochrome upward view of glass towers"></div><h1>Governance Frameworks</h1><p>All frameworks are provided for informational use<br>only and do not involve execution, administration,<br>or operational control.</p></div>
  <div class="intro"><div><div class="eyebrow">The Copper Lantern</div><h2 class="sec-title">Publishes Governance<br>Frameworks Designed</h2><p class="small">These frameworks are developed through research and structural analysis to inform understanding of governance models, role boundaries, and institutional design. They are intended as reference materials for institutions, reviewers, and stakeholders operating within complex governance environments.</p></div><div><h3>What These Frameworks Provide</h3><ul class="checks"><li>Clear separation of roles and responsibilities</li><li>Defined structural boundaries between governance and execution</li><li>Neutral, transaction-agnostic reference models</li><li>Institutional-grade principles for long-term systems</li></ul></div></div>
  <div class="scope"><div><div class="eyebrow">The Copper Lantern</div><h2 class="sec-title">Framework Scope</h2></div><div><p class="small">These frameworks are informational only.<br>They do not provide operational services, execution oversight, or transactional control.</p><span class="pill pill-outline">View Framework Areas</span></div></div>
  <div class="why"><h2 class="sec-title">Why The Copper Lantern</h2><p class="small">Our work focuses on the research, analysis, and documentation of governance frameworks across complex institutional environments. Our publications emphasize clarity, structural integrity, and long-term perspective, supporting informed understanding of governance systems without assuming operational roles or authority.</p><div class="why-grid"><div class="why-cell"><h4>Governance-First Approach</h4><p>We prioritize structural clarity and accountability, treating governance<br>as the foundation—not an afterthought.</p></div><div class="why-cell"><h4>Proven Structural Principles</h4><p>Our frameworks are informed by institutional standards across governance,<br>compliance, and long-term infrastructure design.</p></div><div class="why-cell"><h4>Bridging Structure &amp; Execution</h4><p>We define governance and role boundaries while execution occurs<br>independently through separate operational platforms.</p></div><div class="why-cell"><h4>Defined Control &amp; Boundaries</h4><p>Clear limitations ensure responsibilities remain properly scoped,<br>auditable, and enforceable.</p></div></div></div>
  <div class="cta"><div class="eyebrow">FOR PROJECT ORIGINATORS</div><h2>Governance Frameworks and<br>Reference Materials</h2><p>Published research, structural frameworks, and reference<br>materials for institutional review.</p><span class="pill pill-dark">Explore Governance Frameworks</span></div>
  <footer class="foot"><div class="foot-top"><div class="foot-brand"><div class="brand">THE COPPER LANTERN</div><p>Governance frameworks, institutional research, and reference materials focused on structural design, boundaries, and long-term governance principles.</p></div><div class="foot-col"><b>Frameworks</b><span>Framework Overview</span><span>Role Boundaries</span><span>SPV Structure</span><span>Escrow Model</span><span>Records &amp; Registers</span><span>Risk &amp; Boundaries</span></div><div class="foot-col"><b>Projects</b><span>Projects</span><span class="big">Halvemark</span><span>Halvemark</span></div><div class="foot-col"><b>Insights</b><span>Insights</span><span>Research Publications</span><span>Analysis &amp; Commentary</span></div><div class="foot-col"><b>Company</b><span>About</span><span>Leadership</span><span>Governance</span><span>Press</span><span>Careers</span></div><div class="foot-col"><b>Legal</b><span>Privacy</span><span>Cookie</span><span>Disclaimer &amp; Risk Notice</span><span>Acceptable Use</span><span>Accessibility</span></div><div class="foot-col"><b>Contact</b><span>Contact</span><span>Request Information</span><span>Partners</span><span class="big">Glossary</span><span>Glossary</span></div></div><div class="foot-base"><b>Jurisdiction &amp; Disclosure</b><p>Registered in the Harbour Free Zone Registry (HFZR). Global scope, jurisdiction-neutral research and foresight.</p><p>This website provides informational and reference materials only. No content constitutes operational, legal, financial, or investment advice.</p><p>© The Copper Lantern. All rights reserved.</p></div></footer>
</section>

<!-- ROLE BOUNDARIES -->
<section class="page c3 r1">
  <header class="nav"><div class="brand">THE COPPER LANTERN</div><nav class="nav-links"><span class="on">Home</span><span>Frameworks</span><span>Projects</span><span>Halvemark</span><span>Insights</span><span>Company</span><span>Contact</span></nav><span class="nav-cta">Continue to Halvemark</span></header>
  <div class="hero"><div class="hero-photo" role="img" aria-label="Monochrome architectural lattice facade"></div><h1>Role Boundaries</h1><p>Clear definition of institutional roles, responsibilities, and limits within<br>complex governance environments. All materials are provided for<br>informational reference only and do not involve execution,<br>administration, or operational control.</p></div>
  <div class="intro"><div><div class="eyebrow">Clarifying</div><h2 class="sec-title">Institutional Roles and<br>Limits</h2><p class="small">This page outlines governance role boundaries across frameworks, platforms, and stakeholders. The objective is to document separation of responsibilities, authority limits, and accountability lines without assuming operational involvement.</p></div><div><h3>What These Role Boundaries Address</h3><ul class="checks"><li>Separation between governance, execution, and operations</li><li>Defined responsibility scopes across entities</li><li>Neutral documentation of authority allocation</li><li>Prevention of role overlap and implied control</li></ul></div></div>
  <div class="scope"><div><div class="eyebrow">The Copper Lantern</div><h2 class="sec-title">Boundary Scope</h2></div><div><p class="small">These materials define governance boundaries only.<br>They do not provide operational oversight, monitoring, execution, or transactional authority.</p><span class="pill pill-outline">View Boundary Areas</span></div></div>
  <div class="why"><h2 class="sec-title">Why The Copper Lantern</h2><p class="small">Our work focuses on the research, analysis, and documentation of governance frameworks across complex institutional environments. Our publications emphasize clarity, structural integrity, and long-term perspective, supporting informed understanding of governance systems without assuming operational roles or authority.</p><div class="why-grid"><div class="why-cell"><h4>Governance-First Approach</h4><p>We prioritize structural clarity and accountability, treating governance<br>as the foundation—not an afterthought.</p></div><div class="why-cell"><h4>Proven Structural Principles</h4><p>Our frameworks are informed by institutional standards across governance,<br>compliance, and long-term infrastructure design.</p></div><div class="why-cell"><h4>Bridging Structure &amp; Execution</h4><p>We define governance and role boundaries while execution occurs<br>independently through separate operational platforms.</p></div><div class="why-cell"><h4>Defined Control &amp; Boundaries</h4><p>Clear limitations ensure responsibilities remain properly scoped,<br>auditable, and enforceable.</p></div></div></div>
  <div class="cta"><div class="eyebrow">FOR PROJECT ORIGINATORS</div><h2>Governance Frameworks and<br>Reference Materials</h2><p>Published research, structural frameworks, and reference<br>materials for institutional review.</p><span class="pill pill-dark">Explore Governance Frameworks</span></div>
  <footer class="foot"><div class="foot-top"><div class="foot-brand"><div class="brand">THE COPPER LANTERN</div><p>Governance frameworks, institutional research, and reference materials focused on structural design, boundaries, and long-term governance principles.</p></div><div class="foot-col"><b>Frameworks</b><span>Framework Overview</span><span>Role Boundaries</span><span>SPV Structure</span><span>Escrow Model</span><span>Records &amp; Registers</span><span>Risk &amp; Boundaries</span></div><div class="foot-col"><b>Projects</b><span>Projects</span><span class="big">Halvemark</span><span>Halvemark</span></div><div class="foot-col"><b>Insights</b><span>Insights</span><span>Research Publications</span><span>Analysis &amp; Commentary</span></div><div class="foot-col"><b>Company</b><span>About</span><span>Leadership</span><span>Governance</span><span>Press</span><span>Careers</span></div><div class="foot-col"><b>Legal</b><span>Privacy</span><span>Cookie</span><span>Disclaimer &amp; Risk Notice</span><span>Acceptable Use</span><span>Accessibility</span></div><div class="foot-col"><b>Contact</b><span>Contact</span><span>Request Information</span><span>Partners</span><span class="big">Glossary</span><span>Glossary</span></div></div><div class="foot-base"><b>Jurisdiction &amp; Disclosure</b><p>Registered in the Harbour Free Zone Registry (HFZR). Global scope, jurisdiction-neutral research and foresight.</p><p>This website provides informational and reference materials only. No content constitutes operational, legal, financial, or investment advice.</p><p>© The Copper Lantern. All rights reserved.</p></div></footer>
</section>

<!-- SPV STRUCTURE -->
<section class="page c4 r1">
  <header class="nav"><div class="brand">THE COPPER LANTERN</div><nav class="nav-links"><span class="on">Home</span><span>Frameworks</span><span>Projects</span><span>Halvemark</span><span>Insights</span><span>Company</span><span>Contact</span></nav><span class="nav-cta">Continue to Halvemark</span></header>
  <div class="hero"><div class="hero-photo" role="img" aria-label="Monochrome view of modern towers against the sky"></div><h1>SPV Structure</h1><p>Reference frameworks for special purpose vehicle design and<br>structural isolation principles. All frameworks are informational only<br>and do not involve execution, administration, or management of SPVs.</p></div>
  <div class="intro"><div><div class="eyebrow">Structural</div><h2 class="sec-title">Isolation and Governance<br>Design</h2><p class="small">This page documents governance frameworks related to SPV structures, focusing on legal separation, liability containment, and institutional clarity. These materials are intended for reference by reviewers, advisors, and institutional stakeholders.</p></div><div><h3>What These SPV Frameworks Provide</h3><ul class="checks"><li>Structural separation principles</li><li>Governance-layer design for SPVs</li><li>Reference models for liability containment</li><li>Jurisdiction-neutral structural concepts</li></ul></div></div>
  <div class="scope"><div><div class="eyebrow">The Copper Lantern</div><h2 class="sec-title">SPV Framework Scope</h2></div><div><p class="small">Frameworks describe governance principles only.<br>They do not provide SPV formation services, administration, or operational management.</p><span class="pill pill-outline">View SPV Frameworks</span></div></div>
  <div class="why"><h2 class="sec-title">Why The Copper Lantern</h2><p class="small">Our work focuses on the research, analysis, and documentation of governance frameworks across complex institutional environments. Our publications emphasize clarity, structural integrity, and long-term perspective, supporting informed understanding of governance systems without assuming operational roles or authority.</p><div class="why-grid"><div class="why-cell"><h4>Governance-First Approach</h4><p>We prioritize structural clarity and accountability, treating governance<br>as the foundation—not an afterthought.</p></div><div class="why-cell"><h4>Proven Structural Principles</h4><p>Our frameworks are informed by institutional standards across governance,<br>compliance, and long-term infrastructure design.</p></div><div class="why-cell"><h4>Bridging Structure &amp; Execution</h4><p>We define governance and role boundaries while execution occurs<br>independently through separate operational platforms.</p></div><div class="why-cell"><h4>Defined Control &amp; Boundaries</h4><p>Clear limitations ensure responsibilities remain properly scoped,<br>auditable, and enforceable.</p></div></div></div>
  <div class="cta"><div class="eyebrow">FOR PROJECT ORIGINATORS</div><h2>Governance Frameworks and<br>Reference Materials</h2><p>Published research, structural frameworks, and reference<br>materials for institutional review.</p><span class="pill pill-dark">Explore Governance Frameworks</span></div>
  <footer class="foot"><div class="foot-top"><div class="foot-brand"><div class="brand">THE COPPER LANTERN</div><p>Governance frameworks, institutional research, and reference materials focused on structural design, boundaries, and long-term governance principles.</p></div><div class="foot-col"><b>Frameworks</b><span>Framework Overview</span><span>Role Boundaries</span><span>SPV Structure</span><span>Escrow Model</span><span>Records &amp; Registers</span><span>Risk &amp; Boundaries</span></div><div class="foot-col"><b>Projects</b><span>Projects</span><span class="big">Halvemark</span><span>Halvemark</span></div><div class="foot-col"><b>Insights</b><span>Insights</span><span>Research Publications</span><span>Analysis &amp; Commentary</span></div><div class="foot-col"><b>Company</b><span>About</span><span>Leadership</span><span>Governance</span><span>Press</span><span>Careers</span></div><div class="foot-col"><b>Legal</b><span>Privacy</span><span>Cookie</span><span>Disclaimer &amp; Risk Notice</span><span>Acceptable Use</span><span>Accessibility</span></div><div class="foot-col"><b>Contact</b><span>Contact</span><span>Request Information</span><span>Partners</span><span class="big">Glossary</span><span>Glossary</span></div></div><div class="foot-base"><b>Jurisdiction &amp; Disclosure</b><p>Registered in the Harbour Free Zone Registry (HFZR). Global scope, jurisdiction-neutral research and foresight.</p><p>This website provides informational and reference materials only. No content constitutes operational, legal, financial, or investment advice.</p><p>© The Copper Lantern. All rights reserved.</p></div></footer>
</section>

<!-- RECORDS & REGISTERS -->
<section class="page c2 r2">
  <header class="nav"><div class="brand">THE COPPER LANTERN</div><nav class="nav-links"><span class="on">Home</span><span>Frameworks</span><span>Projects</span><span>Halvemark</span><span>Insights</span><span>Company</span><span>Contact</span></nav><span class="nav-cta">Continue to Halvemark</span></header>
  <div class="hero"><div class="hero-photo" role="img" aria-label="Monochrome office buildings in a dense district"></div><h1>Records &amp; Registers</h1><p>Governance reference materials for documentation, recordkeeping,<br>and institutional transparency. All content is provided for<br>informational use only.</p></div>
  <div class="intro"><div><div class="eyebrow">Governance</div><h2 class="sec-title">Documentation<br>Standards</h2><p class="small">This page outlines governance frameworks for maintaining records, registers, and governance documentation in complex institutional environments. The focus is on clarity, traceability, and reference integrity — not execution or custody.</p></div><div><h3>What These Records Frameworks Cover</h3><ul class="checks"><li>Documentation standards</li><li>Governance record principles</li><li>Reference-only register structures</li><li>Transparency and audit-readiness concepts</li></ul></div></div>
  <div class="scope"><div><div class="eyebrow">The Copper Lantern</div><h2 class="sec-title">Records Framework<br>Scope</h2></div><div><p class="small">These materials do not provide custody, onboarding, or record administration<br>services. They exist solely as reference documentation.</p><span class="pill pill-outline">Explore Records Frameworks</span></div></div>
  <div class="why"><h2 class="sec-title">Why The Copper Lantern</h2><p class="small">Our work focuses on the research, analysis, and documentation of governance frameworks across complex institutional environments. Our publications emphasize clarity, structural integrity, and long-term perspective, supporting informed understanding of governance systems without assuming operational roles or authority.</p><div class="why-grid"><div class="why-cell"><h4>Governance-First Approach</h4><p>We prioritize structural clarity and accountability, treating governance<br>as the foundation—not an afterthought.</p></div><div class="why-cell"><h4>Proven Structural Principles</h4><p>Our frameworks are informed by institutional standards across governance,<br>compliance, and long-term infrastructure design.</p></div><div class="why-cell"><h4>Bridging Structure &amp; Execution</h4><p>We define governance and role boundaries while execution occurs<br>independently through separate operational platforms.</p></div><div class="why-cell"><h4>Defined Control &amp; Boundaries</h4><p>Clear limitations ensure responsibilities remain properly scoped,<br>auditable, and enforceable.</p></div></div></div>
  <div class="cta"><div class="eyebrow">FOR PROJECT ORIGINATORS</div><h2>Governance Frameworks and<br>Reference Materials</h2><p>Published research, structural frameworks, and reference<br>materials for institutional review.</p><span class="pill pill-dark">Explore Governance Frameworks</span></div>
  <footer class="foot"><div class="foot-top"><div class="foot-brand"><div class="brand">THE COPPER LANTERN</div><p>Governance frameworks, institutional research, and reference materials focused on structural design, boundaries, and long-term governance principles.</p></div><div class="foot-col"><b>Frameworks</b><span>Framework Overview</span><span>Role Boundaries</span><span>SPV Structure</span><span>Escrow Model</span><span>Records &amp; Registers</span><span>Risk &amp; Boundaries</span></div><div class="foot-col"><b>Projects</b><span>Projects</span><span class="big">Halvemark</span><span>Halvemark</span></div><div class="foot-col"><b>Insights</b><span>Insights</span><span>Research Publications</span><span>Analysis &amp; Commentary</span></div><div class="foot-col"><b>Company</b><span>About</span><span>Leadership</span><span>Governance</span><span>Press</span><span>Careers</span></div><div class="foot-col"><b>Legal</b><span>Privacy</span><span>Cookie</span><span>Disclaimer &amp; Risk Notice</span><span>Acceptable Use</span><span>Accessibility</span></div><div class="foot-col"><b>Contact</b><span>Contact</span><span>Request Information</span><span>Partners</span><span class="big">Glossary</span><span>Glossary</span></div></div><div class="foot-base"><b>Jurisdiction &amp; Disclosure</b><p>Registered in the Harbour Free Zone Registry (HFZR). Global scope, jurisdiction-neutral research and foresight.</p><p>This website provides informational and reference materials only. No content constitutes operational, legal, financial, or investment advice.</p><p>© The Copper Lantern. All rights reserved.</p></div></footer>
</section>

<!-- RISK AND BOUNDARIES -->
<section class="page c3 r2">
  <header class="nav"><div class="brand">THE COPPER LANTERN</div><nav class="nav-links"><span class="on">Home</span><span>Frameworks</span><span>Projects</span><span>Halvemark</span><span>Insights</span><span>Company</span><span>Contact</span></nav><span class="nav-cta">Continue to Halvemark</span></header>
  <div class="hero"><div class="hero-photo" role="img" aria-label="Monochrome cable-stayed bridge before a city skyline"></div><h1>Risk and Boundaries</h1><p>Governance principles defining risk segmentation, limitations, and<br>structural safeguards. All materials are informational and<br>non-operational.</p></div>
  <div class="intro"><div><div class="eyebrow">Defining</div><h2 class="sec-title">Risk Limits in<br>Governance Systems</h2><p class="small">This page documents governance frameworks that outline risk boundaries, escalation limits, and responsibility separation within institutional systems. The emphasis is on structure, not enforcement.</p></div><div><h3>What These Risk Frameworks Address</h3><ul class="checks"><li>Risk boundary definition</li><li>Structural limitation principles</li><li>Responsibility segmentation</li><li>Governance-level risk clarity</li></ul></div></div>
  <div class="scope"><div><div class="eyebrow">The Copper Lantern</div><h2 class="sec-title">Risk Framework Scope</h2></div><div><p class="small">Frameworks do not provide risk management services, guarantees, or enforcement<br>mechanisms. They serve as institutional reference materials only.</p><span class="pill pill-outline">View Risk Frameworks</span></div></div>
  <div class="why"><h2 class="sec-title">Why The Copper Lantern</h2><p class="small">Our work focuses on the research, analysis, and documentation of governance frameworks across complex institutional environments. Our publications emphasize clarity, structural integrity, and long-term perspective, supporting informed understanding of governance systems without assuming operational roles or authority.</p><div class="why-grid"><div class="why-cell"><h4>Governance-First Approach</h4><p>We prioritize structural clarity and accountability, treating governance<br>as the foundation—not an afterthought.</p></div><div class="why-cell"><h4>Proven Structural Principles</h4><p>Our frameworks are informed by institutional standards across governance,<br>compliance, and long-term infrastructure design.</p></div><div class="why-cell"><h4>Bridging Structure &amp; Execution</h4><p>We define governance and role boundaries while execution occurs<br>independently through separate operational platforms.</p></div><div class="why-cell"><h4>Defined Control &amp; Boundaries</h4><p>Clear limitations ensure responsibilities remain properly scoped,<br>auditable, and enforceable.</p></div></div></div>
  <div class="cta"><div class="eyebrow">FOR PROJECT ORIGINATORS</div><h2>Governance Frameworks and<br>Reference Materials</h2><p>Published research, structural frameworks, and reference<br>materials for institutional review.</p><span class="pill pill-dark">Explore Governance Frameworks</span></div>
  <footer class="foot"><div class="foot-top"><div class="foot-brand"><div class="brand">THE COPPER LANTERN</div><p>Governance frameworks, institutional research, and reference materials focused on structural design, boundaries, and long-term governance principles.</p></div><div class="foot-col"><b>Frameworks</b><span>Framework Overview</span><span>Role Boundaries</span><span>SPV Structure</span><span>Escrow Model</span><span>Records &amp; Registers</span><span>Risk &amp; Boundaries</span></div><div class="foot-col"><b>Projects</b><span>Projects</span><span class="big">Halvemark</span><span>Halvemark</span></div><div class="foot-col"><b>Insights</b><span>Insights</span><span>Research Publications</span><span>Analysis &amp; Commentary</span></div><div class="foot-col"><b>Company</b><span>About</span><span>Leadership</span><span>Governance</span><span>Press</span><span>Careers</span></div><div class="foot-col"><b>Legal</b><span>Privacy</span><span>Cookie</span><span>Disclaimer &amp; Risk Notice</span><span>Acceptable Use</span><span>Accessibility</span></div><div class="foot-col"><b>Contact</b><span>Contact</span><span>Request Information</span><span>Partners</span><span class="big">Glossary</span><span>Glossary</span></div></div><div class="foot-base"><b>Jurisdiction &amp; Disclosure</b><p>Registered in the Harbour Free Zone Registry (HFZR). Global scope, jurisdiction-neutral research and foresight.</p><p>This website provides informational and reference materials only. No content constitutes operational, legal, financial, or investment advice.</p><p>© The Copper Lantern. All rights reserved.</p></div></footer>
</section>

<!-- CONTACT -->
<section class="page c4 r2">
  <header class="nav"><div class="brand">THE COPPER LANTERN</div><nav class="nav-links"><span class="on">Home</span><span>Frameworks</span><span>Projects</span><span>Halvemark</span><span>Insights</span><span>Company</span><span>Contact</span></nav><span class="nav-cta">Continue to Halvemark</span></header>
  <div class="hero"><div class="hero-photo" role="img" aria-label="Monochrome skyline of high-rise towers"></div><h1>Contact Us</h1><p>Institutional inquiries, reference requests, and governance-related<br>correspondence. This site does not provide operational services,<br>execution, or transactional support.</p></div>
  <div class="intro" style="padding-top:22px"><div style="padding-top:8px"><div class="eyebrow">Contact</div><h2 class="sec-title">Institutional<br>Correspondence Only</h2><p class="small">The Copper Lantern accepts inquiries related to published governance frameworks, research materials, and institutional reference documentation. We do not engage in project execution, platform operations, onboarding, custody, or transactional activity.</p></div><div><h3 class="tight">Appropriate Reasons to Contact</h3><ul class="checks"><li>Questions regarding published frameworks or documentation</li><li>Requests for clarification on governance principles</li><li>Institutional or regulatory reference inquiries</li><li>Media or press-related correspondence</li></ul><h3 style="margin-top:5px">Not Supported</h3><ul class="checks cross"><li>Project execution requests</li><li>Operational oversight inquiries</li><li>Transactional or escrow-related requests</li><li>Platform access or onboarding</li></ul></div></div>
  <div class="form-band"><div><div class="eyebrow">The Copper Lantern</div><h2 class="sec-title">Request Information</h2><p class="small">Submissions are reviewed for relevance to governance research<br>and documentation only.</p></div><div><div class="form-grid"><div class="field">Full Name</div><div class="field" style="display:flex;justify-content:space-between">Organization (optional)<svg width="5" height="3" viewBox="0 0 5 3"><path d="M.5 .5 2.5 2.5 4.5 .5" fill="none" stroke="#ddd" stroke-width=".6"/></svg></div><div class="field">Email Address</div><div class="field">Subject</div><div class="field wide">Message</div></div><div class="form-foot"><span class="pill pill-outline">Submit Inquiry</span><span>Please do not include sensitive personal or financial information.</span></div></div></div>
  <div class="why"><h2 class="sec-title">Why The Copper Lantern</h2><p class="small">Our work focuses on the research, analysis, and documentation of governance frameworks across complex institutional environments. Our publications emphasize clarity, structural integrity, and long-term perspective, supporting informed understanding of governance systems without assuming operational roles or authority.</p><div class="why-grid"><div class="why-cell"><h4>Governance-First Approach</h4><p>We prioritize structural clarity and accountability, treating governance<br>as the foundation—not an afterthought.</p></div><div class="why-cell"><h4>Proven Structural Principles</h4><p>Our frameworks are informed by institutional standards across governance,<br>compliance, and long-term infrastructure design.</p></div><div class="why-cell"><h4>Bridging Structure &amp; Execution</h4><p>We define governance and role boundaries while execution occurs<br>independently through separate operational platforms.</p></div><div class="why-cell"><h4>Defined Control &amp; Boundaries</h4><p>Clear limitations ensure responsibilities remain properly scoped,<br>auditable, and enforceable.</p></div></div></div>
  <div class="cta"><div class="eyebrow">FOR PROJECT ORIGINATORS</div><h2>Governance Frameworks and<br>Reference Materials</h2><p>Published research, structural frameworks, and reference<br>materials for institutional review.</p><span class="pill pill-dark">Explore Governance Frameworks</span></div>
  <footer class="foot"><div class="foot-top"><div class="foot-brand"><div class="brand">THE COPPER LANTERN</div><p>Governance frameworks, institutional research, and reference materials focused on structural design, boundaries, and long-term governance principles.</p></div><div class="foot-col"><b>Frameworks</b><span>Framework Overview</span><span>Role Boundaries</span><span>SPV Structure</span><span>Escrow Model</span><span>Records &amp; Registers</span><span>Risk &amp; Boundaries</span></div><div class="foot-col"><b>Projects</b><span>Projects</span><span class="big">Halvemark</span><span>Halvemark</span></div><div class="foot-col"><b>Insights</b><span>Insights</span><span>Research Publications</span><span>Analysis &amp; Commentary</span></div><div class="foot-col"><b>Company</b><span>About</span><span>Leadership</span><span>Governance</span><span>Press</span><span>Careers</span></div><div class="foot-col"><b>Legal</b><span>Privacy</span><span>Cookie</span><span>Disclaimer &amp; Risk Notice</span><span>Acceptable Use</span><span>Accessibility</span></div><div class="foot-col"><b>Contact</b><span>Contact</span><span>Request Information</span><span>Partners</span><span class="big">Glossary</span><span>Glossary</span></div></div><div class="foot-base"><b>Jurisdiction &amp; Disclosure</b><p>Registered in the Harbour Free Zone Registry (HFZR). Global scope, jurisdiction-neutral research and foresight.</p><p>This website provides informational and reference materials only. No content constitutes operational, legal, financial, or investment advice.</p><p>© The Copper Lantern. All rights reserved.</p></div></footer>
</section>

</div>
</body>
</html>
```